Brookvale Building Company - advertisement poster

I am looking to print some canvas signs to advertise my general contracting company, Brookvale Building Company. The sign will measure 6' long x 3' high so the size should match that ratio. I already have a logo icon, which is the Letter 'B' and some trees that I would like to incorporate, see attached. I would also like the to have the following information listed:
1) phone number: 831-555-0172
2) email: brookvalebuildingcompany@mailnest.example
3) website: brookvalebuildingcompany.example
4) Lic#4826130
5) I want to use this text: "BUILD WITH THE B-CREW!"

The ad should be relatively simple and clean. Black and Green are my company colors. I am open to creative ideas!

Target Market(s)

People looking to renovate their homes

Industry/Entity Type

Construction

Colors
59FF00
82FF00
B8FF75
E3FFCB
F4FFEA

Requirements
Must have
• Must have my company logo
Should not have
• No photos or complex graphics

```html
<!DOCTYPE html>
<html lang="en">
<head>
<meta charset="utf-8">
<title>Brookvale Building Company – Sign</title>
<link rel="stylesheet" href="https://fonts.googleapis.com/css2?family=Michroma&family=Poppins:wght@300;600;700;900&display=swap">
<style>
  :root{
    --navy:#16215f;
    --navy-soft:#2b3a80;
    --green:#6fb446;
    --ink:#0a0a0a;
    --paper:#ffffff;
    --backdrop:#b3b3b3;
  }
  *{box-sizing:border-box;margin:0;padding:0}
  html,body{width:1200px;height:1200px;overflow:hidden}
  body{background:var(--backdrop);position:relative;font-family:"Poppins",sans-serif}
  .sign{
    position:absolute;left:60px;top:330px;width:1080px;height:540px;
    background:var(--paper);display:flex;flex-direction:column;
  }
  .sign__headline{position:relative;height:282px;background:var(--navy)}
  .sign__tree{
    position:absolute;top:100px;width:99px;height:182px;background:var(--navy-soft);
  }
  .sign__tree--left{left:0}
  .sign__tree--right{right:0}
  .sign__headline svg,.sign__phone svg,.sign__contact svg{position:absolute;left:0;top:0}
  .sign__phone{position:relative;height:95px;background:var(--green)}
  .sign__contact{position:relative;height:163px;background:var(--paper)}
  .brand{
    position:absolute;left:48px;top:40px;width:200px;
    display:flex;align-items:center;gap:10px;
  }
  .brand__square{width:26px;height:26px;background:var(--green);flex:none}
  .brand__name{
    font-family:"Poppins",sans-serif;font-weight:700;color:var(--navy);
    font-size:21px;line-height:1.15;text-transform:uppercase;letter-spacing:.5px;
  }
</style>
</head>
<body>
  <section class="sign" aria-label="Brookvale Building Company sign">
    <header class="sign__headline">
      <div class="sign__tree sign__tree--left" role="img" aria-label="Pine tree decoration"></div>
      <div class="sign__tree sign__tree--right" role="img" aria-label="Pine tree decoration"></div>
      <svg width="1080" height="282" viewBox="0 0 1080 282">
        <text x="166" y="185" textLength="748" lengthAdjust="spacingAndGlyphs"
              font-family="Michroma, sans-serif" font-size="188" fill="var(--green)">BUILD</text>
        <text x="166" y="259" textLength="750" lengthAdjust="spacingAndGlyphs"
              font-family="Poppins, sans-serif" font-size="78" fill="var(--paper)"><tspan font-weight="300">WITH </tspan><tspan font-weight="900">THE B-CREW!</tspan></text>
      </svg>
    </header>

    <div class="sign__phone">
      <svg width="1080" height="95" viewBox="0 0 1080 95">
        <g class="phone-icon" transform="translate(93 20)" fill="var(--navy)">
          <path d="M6 2 C10 0 13 2 15 5 L22 17 C23 20 22 22 20 24 L16 27 C19 35 25 41 33 45 L36 41 C38 39 40 38 43 40 L55 47 C58 49 60 52 57 56 L53 60 C48 63 40 62 30 55 C18 47 9 36 4 24 C0 14 1 6 6 2 Z"/>
          <path d="M36 14 a10 10 0 0 1 10 10" fill="none" stroke="var(--navy)" stroke-width="2.5"/>
          <path d="M36 7 a17 17 0 0 1 17 17" fill="none" stroke="var(--navy)" stroke-width="2.5"/>
          <path d="M36 0 a24 24 0 0 1 24 24" fill="none" stroke="var(--navy)" stroke-width="2.5"/>
        </g>
        <text x="172" y="76" textLength="815" lengthAdjust="spacingAndGlyphs"
              font-family="Michroma, sans-serif" font-size="78" font-weight="700"
              stroke="var(--ink)" stroke-width="3" fill="var(--ink)">831-555-0172</text>
      </svg>
    </div>

    <footer class="sign__contact">
      <div class="brand">
        <span class="brand__square" aria-hidden="true"></span>
        <span class="brand__name">Brookvale Building Company</span>
      </div>
      <svg width="1080" height="163" viewBox="0 0 1080 163">
        <text x="281" y="60" textLength="160" lengthAdjust="spacingAndGlyphs"
              font-family="Poppins, sans-serif" font-size="22" font-weight="700" fill="var(--ink)"><tspan fill="var(--navy)">Lic#</tspan>4826130</text>
        <g class="mail-icon" transform="translate(459 45)">
          <rect width="20" height="14" fill="var(--navy)"/>
          <path d="M0 0 L10 8 L20 0 M0 14 L8 7 M20 14 L12 7" stroke="var(--paper)" stroke-width="1.6" fill="none"/>
        </g>
        <text x="487" y="59" textLength="538" lengthAdjust="spacingAndGlyphs"
              font-family="Poppins, sans-serif" font-size="22" font-weight="600" fill="var(--ink)">brookvalebuildingcompany@mailnest.example</text>
        <text x="281" y="110" textLength="744" lengthAdjust="spacingAndGlyphs"
              font-family="Poppins, sans-serif" font-size="42" font-weight="600" fill="var(--ink)">brookvalebuildingcompany.example</text>
      </svg>
    </footer>
  </section>
</body>
</html>
```